KVOR Individual and Corporate Development Business Card Design

KVOR needs a business card design that is aligned with it's values and targetted markets. Coherent Lattice of Adaptive Reasoning Method's self diagnosis model and tools, which can be used for personal improvement and team/business performance enhancement, is based on the learnings of over 20 years of medical practitioning. KVOR supercharges personal effectiveness and awareness to also increase team and business performance.

The targetted markets are high performance individuals and teams who aspire seek to enhance their capabilities and achieve their absolute best potential.

Look and feel for the business card design we are looking for is high technology, premium, fresh, new and medical.

Target Market(s)

Industry/Entity Type

Business Consultant

Contact Information for Business Card

Logo, Full Name, Title, Phone number, Email, company name, Address,

Font styles to use
Sans Serif

Requirements
Must have
• Tag line: Maximising Performance for Highly Effective People
• Please use same colours as the logo.

```html
<!DOCTYPE html>
<html lang="en">
<head>
<meta charset="utf-8">
<title>KVOR Business Card</title>
<link rel="stylesheet" href="https://fonts.googleapis.com/css2?family=Lato:wght@400;700&family=Roboto:wght@500;700&display=swap">
<style>
  :root {
    --backdrop: #7b7b7b;
    --teal: #0aa4c2;
    --card-white: #ffffff;
    --card-black: #101010;
    --ink: #1c1c1c;
    --rule: #555555;
  }
  * { margin: 0; padding: 0; box-sizing: border-box; }
  html, body { width: 1200px; height: 900px; overflow: hidden; }
  body {
    background: var(--backdrop);
    position: relative;
    font-family: "Lato", sans-serif;
    color: var(--ink);
  }
  .card {
    position: absolute;
    top: 306px;
    width: 439px;
    height: 270px;
    border-radius: 12px;
    overflow: hidden;
    box-shadow: 3px 4px 8px rgba(0,0,0,0.35);
  }
  .card-front { left: 149px; background: var(--card-white); }
  .card-back { left: 609px; background: var(--card-black); }

  .brand-front {
    position: absolute;
    left: 205px;
    top: 52px;
    width: 190px;
    text-align: center;
  }
  .brand-name {
    font-family: "Roboto", sans-serif;
    font-weight: 700;
    color: var(--teal);
    font-size: 50px;
    line-height: 1;
    letter-spacing: 2px;
  }
  .brand-descriptor {
    margin-top: 6px;
    font-family: "Roboto", sans-serif;
    font-weight: 500;
    color: var(--teal);
    font-size: 9.5px;
    line-height: 1.25;
    text-transform: uppercase;
    letter-spacing: 0.3px;
  }

  .person-name {
    position: absolute;
    left: 23px;
    top: 154px;
    font-family: "Roboto", sans-serif;
    font-weight: 700;
    font-size: 14px;
    color: var(--teal);
    letter-spacing: 0.3px;
  }
  .person-title {
    position: absolute;
    left: 23px;
    top: 170px;
    font-size: 12px;
  }
  .title-rule {
    position: absolute;
    left: 138px;
    top: 178px;
    width: 278px;
    height: 1px;
    background: var(--rule);
  }
  .contact-list {
    position: absolute;
    left: 23px;
    top: 200px;
    list-style: none;
    font-size: 12.5px;
    line-height: 16px;
  }
  .contact-list li { display: flex; align-items: center; gap: 5px; }
  .contact-list svg { width: 9px; height: 9px; fill: var(--teal); flex: none; }
  .address {
    position: absolute;
    right: 23px;
    top: 216px;
    font-size: 12.5px;
    line-height: 16px;
    text-align: right;
  }

  .brand-back {
    position: absolute;
    left: 0;
    width: 100%;
    top: 84px;
    text-align: center;
    font-family: "Roboto", sans-serif;
    font-weight: 700;
    color: var(--teal);
    font-size: 62px;
    line-height: 1;
    letter-spacing: 3px;
  }
  .tagline-band {
    position: absolute;
    left: 0;
    top: 201px;
    width: 100%;
    height: 40px;
    background: var(--teal);
    display: flex;
    align-items: center;
    justify-content: center;
    font-size: 13px;
    letter-spacing: 0.2px;
    text-transform: uppercase;
    color: var(--ink);
  }
</style>
</head>
<body>
  <section class="card card-front">
    <div class="brand-front">
      <div class="brand-name">KVOR</div>
      <div class="brand-descriptor">Coherent Lattice of Adaptive Reasoning Method</div>
    </div>

    <div class="person-name">DANIEL HART</div>
    <div class="person-title">Managing Director</div>
    <div class="title-rule"></div>

    <ul class="contact-list">
      <li>
        <svg viewBox="0 0 10 10" aria-hidden="true"><path d="M2 0.5 L3.6 2.6 L2.8 3.6 Q4 6 6.4 7.2 L7.4 6.4 L9.5 8 L8.6 9.5 Q3 9 0.5 1.4 Z"/></svg>
        <span>(044)987650321</span>
      </li>
      <li>
        <svg viewBox="0 0 10 10" aria-hidden="true"><path d="M0 2 H10 V8.5 H0 Z M0.6 2.4 L5 5.6 L9.4 2.4" stroke="#fff" stroke-width="0.8"/></svg>
        <span>hello@kvormail.com</span>
      </li>
      <li>
        <svg viewBox="0 0 10 10" aria-hidden="true"><circle cx="5" cy="5" r="5"/><path d="M0 5 H10 M5 0 Q2.5 5 5 10 M5 0 Q7.5 5 5 10" stroke="#fff" stroke-width="0.7" fill="none"/></svg>
        <span>www.kvorsite.com</span>
      </li>
    </ul>

    <div class="address">5678, Harbour Lane,<br>Country name, 67890</div>
  </section>

  <section class="card card-back">
    <div class="brand-back">KVOR</div>
    <div class="tagline-band">Maximising Performance for Highly Effective People</div>
  </section>
</body>
</html>
```